Website for new dental office

I am Dr. Colin Ashford and am building a new dental practice. I specialize in general dentistry. I am young and have a higher end dental practice incorporating very new technologies and would like my website to reflect that. As many dental patients are older, the website must be very easy to navigate. I would like patients to be able to request appointments, and will eventually add on patient information forms (the health history, etc, that you normally fill out in the practice) from my practice management software, so leave an area for that.

Industry/Entity Type

Building

```html
<!DOCTYPE html>
<html lang="en">
<head>
<meta charset="utf-8">
<title>Ashford Dental – Page Designs</title>
<link rel="stylesheet" href="https://fonts.googleapis.com/css2?family=Raleway:wght@400&family=Open+Sans:ital,wght@0,400;0,700;1,400&display=swap">
<style>
:root{
  --stage:#ececec;
  --paper:#ffffff;
  --ink:#1c1c1c;
  --muted:#8a8a8a;
  --rule:#dcdcdc;
  --nav-active:#111111;
  --band:#262626;
  --photo-team:linear-gradient(120deg,#e9eef2 0%,#bcd3e0 45%,#8fb4c9 100%);
  --photo-office:linear-gradient(100deg,#cfd6d8 0%,#e9ecec 40%,#9aa58e 100%);
  --photo-thumb:linear-gradient(135deg,#d8dde0,#9fb0b9);
  --teal:#3fb6a8;
  --slate:#5b6770;
  --coral:#c9574f;
}
*{box-sizing:border-box;margin:0;padding:0}
html,body{width:1200px;height:496px;overflow:hidden}
body{background:var(--stage);font-family:"Open Sans",Arial,sans-serif;color:var(--ink);position:relative}

/* Pages are laid out at double size and scaled down so small text renders reliably */
.page{position:absolute;top:20px;width:752px;height:912px;background:var(--paper);overflow:hidden;box-shadow:0 4px 20px rgba(0,0,0,.08);transform:scale(.5);transform-origin:0 0}
.page--team{left:18px}.page--about{left:412px}.page--resources{left:806px}

.sidebar{position:absolute;left:0;top:0;width:132px;height:100%;background:var(--paper);border-right:2px solid var(--rule);z-index:2}
.brand{padding:30px 8px 28px;text-align:center;font-family:"Open Sans",Arial,sans-serif;font-weight:400;font-size:13px;letter-spacing:0;color:var(--ink);white-space:nowrap}
.nav{list-style:none}
.nav li{height:52px;line-height:52px;font-family:"Raleway",Arial,sans-serif;font-size:9.5px;letter-spacing:1px;text-align:center;color:var(--muted);border-top:2px solid var(--rule);white-space:nowrap}
.nav li.is-active{background:var(--nav-active);color:#fff}
.content{position:absolute;left:132px;top:0;right:0;bottom:0}

.photo{display:block}
.hero-team{height:340px;background:var(--photo-team)}
.section-title{font-family:"Raleway",Arial,sans-serif;font-weight:400;font-size:16px;letter-spacing:4px;text-align:center;margin:36px 0 28px}
.section-title::after{content:"";display:block;width:80px;height:2px;background:var(--rule);margin:12px auto 0}
.dentists{display:flex;justify-content:center;gap:32px}
.dentist{width:116px;text-align:center}
.dentist h3{font-size:14px;font-weight:700;letter-spacing:1px}
.dentist .role{font-size:9px;color:var(--muted);margin:4px 0 12px;letter-spacing:1px}
.dentist p{font-size:9px;line-height:1.5;color:var(--muted)}
.dentist .dot{width:32px;height:32px;border-radius:50%;margin:24px auto 0;border:6px solid #e3e3e3}
.dot--teal{background:var(--teal)}.dot--slate{background:var(--slate)}.dot--coral{background:var(--coral)}

.hero-office{height:180px;background:var(--photo-office);position:relative}
.hero-label{position:absolute;left:50%;top:56px;transform:translateX(-50%);background:var(--paper);padding:12px 20px;font-family:"Raleway",Arial,sans-serif;font-size:16px;letter-spacing:4px;border:2px solid var(--rule);white-space:nowrap;color:var(--ink)}
.intro{width:400px;margin:48px auto 0;font-size:9.6px;line-height:1.7;color:var(--muted);text-align:center}
.detail{width:400px;margin:0 auto 32px}
.detail h4{font-size:17px;font-weight:700}
.detail em{display:block;font-size:10px;margin:4px 0 16px}
.detail p{font-size:9.6px;line-height:1.7;color:var(--muted)}

.res-head{height:104px;background:var(--band);position:relative}
.res-head .hero-label{top:12px}
.res-date{position:absolute;right:20px;bottom:12px;font-size:9px;color:#bbb;letter-spacing:1px}
.res-search{position:absolute;left:50%;bottom:12px;transform:translateX(-50%);width:240px;height:16px;background:var(--paper)}
.article{display:flex;gap:16px;padding:36px 40px}
.thumb{width:92px;height:68px;background:var(--photo-thumb);flex:none}
.article h4{font-size:14px;font-style:italic;font-weight:400}
.article time{display:block;font-size:9px;font-weight:700;margin:4px 0 8px}
.article p{font-size:9px;line-height:1.6;color:var(--muted)}
.article .more{display:block;margin-top:8px;font-size:9px;color:var(--ink)}
.res-band{height:68px;background:var(--band);position:relative;margin-top:12px}
.res-band svg{position:absolute;right:20px;top:8px}
</style>
</head>
<body>

<section class="page page--team">
  <aside class="sidebar">
    <div class="brand">Ashford Dental</div>
    <ul class="nav"><li>SERVICES</li><li class="is-active">TEAM</li><li>ABOUT</li><li>PATIENT RESOURCES</li><li>CONTACT US</li></ul>
  </aside>
  <main class="content">
    <div class="photo hero-team" role="img" aria-label="Photo of the dental team in scrubs and white coats"></div>
    <h2 class="section-title">DENTISTS</h2>
    <div class="dentists">
      <article class="dentist"><h3>MAREN</h3><div class="role">General, DDS</div><p>Gentle care for every age, with a calm chair-side manner and clear answers.</p><div class="dot dot--teal"></div></article>
      <article class="dentist"><h3>TOBIAS</h3><div class="role">General, DDS</div><p>Careful, modern treatment planned around you, explained in plain words every step.</p><div class="dot dot--slate"></div></article>
      <article class="dentist"><h3>COLIN</h3><div class="role">General, DDS</div><p>New technology and patient comfort come first in every single visit here.</p><div class="dot dot--coral"></div></article>
    </div>
  </main>
</section>

<section class="page page--about">
  <aside class="sidebar">
    <div class="brand">Ashford Dental</div>
    <ul class="nav"><li>SERVICES</li><li>TEAM</li><li class="is-active">ABOUT</li><li>PATIENT RESOURCES</li><li>CONTACT US</li></ul>
  </aside>
  <main class="content">
    <div class="photo hero-office" role="img" aria-label="Photo of a modern treatment room beside a garden view"><span class="hero-label">OUR OFFICE</span></div>
    <p class="intro">Our office pairs modern digital imaging with a quiet, welcoming space. Every room is built for comfort, and every visit starts on time with a friendly face at the front desk.</p>
    <h2 class="section-title">DETAILS</h2>
    <div class="detail">
      <h4>Nunc dictum ipsum no</h4>
      <em>Proin venenatis sapien porttitor ligula pharetra, in condimentum justo sollicitudin.</em>
      <p>Digital x-rays cut exposure and show results in seconds. Same-day crowns mean fewer visits and less time away from work.</p>
    </div>
    <div class="detail">
      <h4>Cras leo nibh</h4>
      <em>Comfort built into every visit.</em>
    </div>
  </main>
</section>

<section class="page page--resources">
  <aside class="sidebar">
    <div class="brand">Ashford Dental</div>
    <ul class="nav"><li>SERVICES</li><li>TEAM</li><li>ABOUT</li><li class="is-active">PATIENT RESOURCES</li><li>CONTACT US</li></ul>
  </aside>
  <main class="content">
    <header class="res-head"><span class="hero-label">RESOURCES</span><span class="res-search"></span><span class="res-date">Monday 21 July</span></header>
    <article class="article">
      <div class="thumb" role="img" aria-label="Photo of dental instruments on a tray"></div>
      <div><h4>Morbi tristique elementum</h4><time>01.08.2014</time><p>Learn how to brush and floss the right way, and what to expect at your first cleaning with our team.</p><span class="more">Read more</span></div>
    </article>
    <div class="res-band"><svg width="20" height="12" viewBox="0 0 20 12"><path d="M2 10 L10 2 L18 10" fill="none" stroke="#ffffff" stroke-width="2"/></svg></div>
    <article class="article">
      <div class="thumb" role="img" aria-label="Photo of a dental chair in a treatment room"></div>
      <div><h4>Pellentesque eu sagittis</h4><time>23.06.2014</time><p>Forms for health history and insurance will be ready here soon.</p></div>
    </article>
  </main>
</section>

</body>
</html>
```